business card deign

Logo needs the following on it.
1. attached logo
2. Tagline - "From the cooler to the crowd...we keep it all rolling!"
3. Name- Dalton Pikes, Founder and CPO
4. Address - 412 E. Carver Avenue, Ste 2207, Tampa, FL. 33917
5. Phone - 555.318.4726

```html
<!DOCTYPE html>
<html lang="en">
<head>
<meta charset="UTF-8">
<title>Bravlo Business Card</title>
<link rel="stylesheet" href="https://fonts.googleapis.com/css2?family=Montserrat:wght@700;800&family=Roboto:wght@300;400&family=Lato:wght@400&display=swap">
<style>
  :root {
    --bg: #1c1c1f;
    --card-white: #ffffff;
    --card-black: #0e0e10;
    --ink: #111111;
    --ink-soft: #3a3a3a;
    --rule: #555555;
    --silver-light: #c9c9cc;
    --silver-dark: #2a2a2d;
  }
  * { box-sizing: border-box; margin: 0; padding: 0; }
  html, body {
    width: 1200px; height: 800px; overflow: hidden;
    background: var(--bg);
  }
  .stage {
    width: 1200px; height: 800px;
    display: flex; align-items: center; justify-content: center; gap: 40px;
  }
  .card {
    width: 540px; height: 309px;
    border-radius: 26px;
    overflow: hidden;
    position: relative;
  }
  .card-back { background: var(--card-black); }
  .pattern-fill {
    position: absolute; inset: 0;
    background: linear-gradient(135deg, var(--silver-light) 0%, #6d6d72 35%, var(--silver-dark) 70%, #1a1a1c 100%);
    opacity: 0.55;
  }
  .card-front {
    background: var(--card-white);
    color: var(--ink);
    display: flex;
  }
  .brand {
    width: 250px;
    padding: 0 18px;
    display: flex; flex-direction: column; align-items: center; justify-content: center;
    gap: 10px;
  }
  .brand-row { display: flex; align-items: center; gap: 10px; }
  .brand-dot { width: 18px; height: 18px; border-radius: 50%; background: var(--ink); flex: none; }
  .brand-name {
    font-family: "Montserrat", sans-serif; font-weight: 800;
    font-size: 28px; letter-spacing: 6px; color: var(--ink);
  }
  .tagline {
    font-family: "Lato", sans-serif; font-size: 9.5px; color: var(--ink);
    text-align: center; white-space: nowrap;
  }
  .divider {
    width: 1px; background: var(--rule); margin: 60px 0;
    flex: none;
  }
  .details {
    flex: 1; padding: 58px 0 0 30px;
    font-family: "Roboto", sans-serif; font-weight: 300; color: var(--ink-soft);
  }
  .person-name {
    font-family: "Montserrat", sans-serif; font-weight: 700;
    font-size: 22px; color: var(--ink); letter-spacing: 0.3px;
  }
  .person-title { font-size: 16px; margin-top: 2px; }
  .address { font-size: 15px; line-height: 1.3; margin-top: 16px; }
  .contact { list-style: none; margin-top: 12px; font-size: 15px; }
  .contact li { display: flex; align-items: center; gap: 8px; line-height: 1.45; }
  .contact svg { width: 14px; height: 14px; fill: var(--ink); flex: none; }
</style>
</head>
<body>
<main class="stage">
  <section class="card card-back">
    <div class="pattern-fill" role="img" aria-label="Repeating metallic silver emblem pattern on black"></div>
  </section>

  <section class="card card-front">
    <div class="brand">
      <div class="brand-row">
        <span class="brand-dot"></span>
        <span class="brand-name">BRAVLO</span>
      </div>
      <p class="tagline">From the cooler to the crowd...we keep it all rolling!</p>
    </div>
    <div class="divider"></div>
    <div class="details">
      <h1 class="person-name">DALTON PIKES</h1>
      <p class="person-title">Founder and CPO</p>
      <p class="address">412 E. Carver Avenue,<br>Ste 2207, Tampa, FL. 33917</p>
      <ul class="contact">
        <li>
          <svg viewBox="0 0 24 24" aria-hidden="true"><path d="M6.6 10.8a15.1 15.1 0 0 0 6.6 6.6l2.2-2.2c.3-.3.7-.4 1-.2 1.1.4 2.3.6 3.6.6.6 0 1 .4 1 1V20c0 .6-.4 1-1 1A17 17 0 0 1 3 4c0-.6.4-1 1-1h3.5c.6 0 1 .4 1 1 0 1.3.2 2.5.6 3.6.1.3 0 .7-.2 1z"/></svg>
          555.318.4726
        </li>
        <li>
          <svg viewBox="0 0 24 24" aria-hidden="true"><path d="M2 5h20v14H2zm2 2v.5l8 5 8-5V7z"/></svg>
          info@bravlogear.com
        </li>
      </ul>
    </div>
  </section>
</main>
</body>
</html>
```